Heron Haulage needs Bussiness cards!

Our new trucking company needs business cards!
We need the same design with two different names and emails, everything else it's the same.
I have included our original logo so we can use it for the design.
Note: the logo to be used is the o e with the buffalo on the right side, next to the letters H and H.

Target Market(s)

Trucking, refrigerated transportation, freight

Industry/Entity Type

Business

Contact Information for Business Card

Card #1:
Marcus Whitfield
marcuswhitfield@heronhaulage.example
1-855-317-6094
(956)238-7160
4117 W. Larkin Ave.
Pharr, TX 78590
www.heronhaulage.example

Card#2:
Rosalba Quintero
rosalba@heronhaulage.example
1-855-317-6094
(956)238-7160
4117 W. Larkin Ave.
Pharr, TX 78590
www.heronhaulage.example

Font styles to use
Sans Serif

Colors
0655a3
ec1f27
ffffff

Requirements
Must have
• our logo
Nice to have
• roads on background,

```html
<!DOCTYPE html>
<html lang="en">
<head>
<meta charset="utf-8">
<title>Heron Haulage – Business Cards</title>
<link rel="stylesheet" href="https://fonts.googleapis.com/css2?family=Source+Sans+3:wght@400;600;800&display=swap">
<style>
  :root {
    --navy: #0b2c5a;
    --red: #b3141f;
    --white: #ffffff;
    --backdrop: #ecebe8;
    --shadow: rgba(0, 0, 0, 0.18);
  }
  * { margin: 0; padding: 0; box-sizing: border-box; }
  html, body { width: 1200px; height: 900px; overflow: hidden; }
  body {
    background: var(--backdrop);
    font-family: "Source Sans 3", Arial, sans-serif;
    position: relative;
  }
  .card {
    position: absolute;
    box-shadow: 0 6px 18px var(--shadow);
    overflow: hidden;
  }
  .card-front {
    left: 78px; top: 35px; width: 588px; height: 363px;
    background: var(--white);
  }
  .front-band { position: absolute; left: 0; top: 0; width: 588px; height: 363px; }
  .brand-name {
    position: absolute;
    left: 132px; top: 58px; width: 330px;
    color: var(--navy);
    font-weight: 800;
    font-size: 46px;
    line-height: 44px;
    letter-spacing: -0.5px;
  }
  .contact-list {
    position: absolute;
    right: 284px; top: 235px;
    list-style: none;
    color: var(--white);
    font-size: 14px;
    line-height: 23.5px;
    text-align: right;
    white-space: nowrap;
  }
  .contact-list li { display: flex; align-items: center; justify-content: flex-end; gap: 6px; }
  .contact-list svg { width: 12px; height: 12px; fill: var(--white); flex: none; }
  .person {
    position: absolute;
    left: 322px; top: 238px;
    color: var(--white);
    white-space: nowrap;
  }
  .person-name { font-size: 21px; font-weight: 600; margin-bottom: 14px; }
  .person-address { font-size: 14px; line-height: 23.5px; }
  .card-back {
    left: 388px; top: 505px; width: 566px; height: 352px;
    background: var(--red);
    color: var(--white);
    text-align: center;
  }
  .back-brand {
    position: absolute; left: 0; right: 0; top: 158px;
    font-weight: 800; font-size: 50px; line-height: 48px; letter-spacing: -0.5px;
  }
  .back-web {
    position: absolute; left: 0; right: 0; top: 290px;
    font-size: 15px;
  }
</style>
</head>
<body>
  <section class="card card-front" aria-label="Business card front">
    <svg class="front-band" viewBox="0 0 588 363" aria-hidden="true">
      <path d="M0,182 L440,182 C520,182 570,215 588,250 V363 H0 Z" fill="var(--navy)"/>
      <path d="M0,172 C220,168 440,160 520,170 C560,176 584,212 588,250 C570,215 520,184 440,184 L0,184 Z" fill="var(--red)"/>
    </svg>
    <div class="brand-name">Heron<br>Haulage</div>

    <ul class="contact-list">
      <li>1-855-317-6094
        <svg viewBox="0 0 12 12"><path d="M2.5 0.8l2 2.2-1 1.2c.6 1.5 1.7 2.6 3.3 3.3l1.2-1 2.2 2-1.2 2C5.5 10.2 1.8 6.5.6 2z"/></svg></li>
      <li>(956)238-7160
        <svg viewBox="0 0 12 12"><path d="M3 0h6a1 1 0 0 1 1 1v10a1 1 0 0 1-1 1H3a1 1 0 0 1-1-1V1a1 1 0 0 1 1-1zm.5 1.5v7.5h5V1.5zM6 9.8a.7.7 0 1 0 0 1.4.7.7 0 0 0 0-1.4z"/></svg></li>
      <li>marcuswhitfield@heronhaulage.example
        <svg viewBox="0 0 12 12"><path d="M0 2h12v8H0zm1 1v.4l5 3.2 5-3.2V3zm0 1.6V9h10V4.6L6 7.8z"/></svg></li>
      <li>www.heronhaulage.example
        <svg viewBox="0 0 12 12"><circle cx="6" cy="6" r="5.5"/></svg></li>
    </ul>

    <div class="person">
      <div class="person-name">Marcus Whitfield</div>
      <div class="person-address">4117 W. Larkin Ave.<br>Pharr, TX 78590</div>
    </div>
  </section>

  <section class="card card-back" aria-label="Business card back">
    <div class="back-brand">Heron<br>Haulage</div>
    <div class="back-web">www.heronhaulage.example</div>
  </section>
</body>
</html>
```